Dental office stationary (letterhead, envelopes), business cards, presentation folders

Nothing too dental outside of the logo. I will need all stationary, presentation folders, business cards. Would prefer to stay in the colors of the logo

Gordon Patel, DDS
Bright Haven Dental Implant Center
555-318-2790
info@brighthavendental.example
4817 NW Maple Crest Rd Unit B
Harbor Vale, ST 00000

Also need appointment date and time
And cancellation policy
I want it to say “kindly ask for
A 48hr cancellation policy to avoid incurring a cancellation fee”

Industry/Entity Type

Dental

Colors
0054AA
0677BA
7BADD7
CADEEF
E8F1F8

Requirements
Must have
• Name of your office, name of doctor, address, phone number
Should not have
• Too much tooth/dental. Only the tooth in logo

```html
<!DOCTYPE html>
<html lang="en">
<head>
<meta charset="utf-8">
<title>Bright Haven Dental Implant Center – Stationery</title>
<link href="https://fonts.googleapis.com/css2?family=Roboto:wght@400;500;700&display=swap" rel="stylesheet">
<style>
  :root{
    --bg:#cbcbcb;
    --sky:#19c0ef;
    --blue:#0b6cc0;
    --deep:#0a5aa8;
    --teal:#1ebc9c;
    --ink:#333;
    --muted:#555;
    --paper:#ffffff;
    --ghost:#e8f1f8;
  }
  *{box-sizing:border-box;margin:0;padding:0}
  html,body{width:1200px;height:1011px;overflow:hidden}
  body{background:var(--bg);font-family:'Roboto',Arial,sans-serif;position:relative;color:var(--ink)}
  .piece{position:absolute;background:var(--paper);overflow:hidden;box-shadow:0 3px 6px rgba(0,0,0,.25)}
  .card{border-radius:14px}
  .abs{position:absolute}

  .brand{position:absolute;text-align:center;font-weight:400;color:var(--blue);line-height:1}
  .brand .name{display:block;letter-spacing:.5px}
  .brand .sub{display:block;text-transform:uppercase;letter-spacing:2px;margin-top:3px}
  .brand.white{color:#fff}

  .contacts li{list-style:none;display:flex;align-items:center;gap:3px}
  .contacts svg{width:7px;height:7px;fill:currentColor;flex:none}

  /* business card front */
  .card-front{left:53px;top:99px;width:325px;height:185px}
  .card-front .art{position:absolute;inset:0}
  .card-front .doctor{left:16px;top:34px;color:#fff;font-weight:700;font-size:11px}
  .card-front .address{left:16px;top:76px;color:#fff;font-size:8.4px;line-height:11px}
  .card-front .contacts{left:16px;top:117px;color:#fff;font-size:8.4px;line-height:10.6px}
  .card-front .brand{left:168px;top:82px;width:140px}
  .card-front .brand .name{font-size:17px}
  .card-front .brand .sub{font-size:5px}

  /* appointment card */
  .appt{left:53px;top:315px;width:325px;height:186px}
  .appt .band{position:absolute;left:0;top:0;width:100%;height:66px;background:linear-gradient(90deg,var(--sky),var(--blue))}
  .appt .rule{position:absolute;left:0;top:68px;width:100%;height:3px;background:var(--teal)}
  .appt .tab{position:absolute;left:83px;top:68px;width:159px;height:15px;background:var(--teal);clip-path:polygon(0 0,100% 0,92% 100%,8% 100%);color:#fff;font-size:12px;text-align:center;line-height:16px}
  .appt .brand{left:0;top:16px;width:100%}
  .appt .brand .name{font-size:20px}
  .appt .brand .sub{font-size:6px}
  .appt .dash{position:absolute;left:21px;right:21px;top:110px;border-top:1px dashed #aaa}
  .appt .fields{position:absolute;left:21px;right:21px;top:127px;font-size:9.5px;color:var(--muted);display:flex;align-items:flex-end;gap:3px}
  .appt .fields .line{flex:1;border-bottom:1px solid #999;height:8px}
  .appt .notice{position:absolute;left:30px;right:30px;top:151px;font-size:8.4px;line-height:10.5px;text-align:center;color:var(--muted)}

  /* letterhead */
  .letter{left:402px;top:97px;width:286px;height:404px}
  .letter .brand{left:20px;top:22px;width:102px}
  .letter .brand .name{font-size:13px}
  .letter .brand .sub{font-size:4px;letter-spacing:1.2px}
  .letter .head-info{left:203px;top:19px;font-size:4.4px;line-height:5.6px;color:var(--muted)}
  .letter .head-info .contacts{margin-top:3px}
  .letter .head-info .contacts svg{width:4px;height:4px;fill:var(--teal)}
  .letter .head-info .web{color:var(--teal)}
  .letter .head-rule{left:20px;right:20px;top:54px;border-top:.8px solid #777}
  .letter .greet{left:26px;top:124px;font-size:6.6px;font-weight:500}
  .letter .body{left:26px;right:26px;top:143px;font-size:4.55px;line-height:5.8px;color:var(--muted);text-align:justify}
  .letter .body p{margin-bottom:5.5px}
  .letter .close{left:26px;top:264px;font-size:3.8px;font-weight:500}
  .letter .sign{left:27px;top:280px;width:36px;height:10px;background:linear-gradient(90deg,#d6d6d6,#eeeeee);border-radius:5px}
  .ghost-circle{position:absolute;border-radius:50%;border:22px solid var(--ghost)}
  .letter .ghost-circle{left:170px;top:280px;width:124px;height:124px}

  /* envelope back */
  .env-back{left:715px;top:99px;width:431px;height:186px}
  .env-back .brand{left:15px;top:17px;width:88px}
  .env-back .brand .name{font-size:12.5px}
  .env-back .brand .sub{font-size:3.8px;letter-spacing:1.2px}
  .env-back .address{left:15px;top:47px;font-size:6.4px;line-height:8px;color:var(--muted)}
  .env-back .ghost-circle{left:285px;top:40px;width:145px;height:145px}

  /* envelope front */
  .env-front{left:713px;top:312px;width:435px;height:189px}
  .env-front .flap{position:absolute;left:0;top:0;width:100%;height:52px;background:linear-gradient(90deg,var(--sky),var(--blue));clip-path:polygon(0 0,100% 0,98% 70%,95% 100%,5% 100%,2% 70%)}
  .env-front .brand{left:0;top:12px;width:100%}
  .env-front .brand .name{font-size:15px}
  .env-front .brand .sub{font-size:4.2px;letter-spacing:1.4px}

  /* folders */
  .folder{position:absolute;top:572px;width:540px;height:368px;display:flex;box-shadow:0 8px 18px rgba(0,0,0,.25)}
  .folder .panel{position:relative;width:50%;height:100%;overflow:hidden}
  .folder-outside{left:40px}
  .folder-outside .back{background:linear-gradient(135deg,#0c66b8,#0a4f99)}
  .folder-outside .front{background:linear-gradient(135deg,#0e6fc2,#0a56a2);border-left:1px solid rgba(0,0,0,.15)}
  .folder-outside .back .contacts{left:18px;bottom:20px;color:#fff;font-size:6.4px;line-height:8.5px;opacity:.9}
  .folder-outside .front .ghost-circle{left:30px;top:70px;width:210px;height:210px;border-color:rgba(255,255,255,.05);border-width:34px}
  .folder-outside .front .brand{left:0;top:158px;width:100%}
  .folder-outside .front .brand .name{font-size:24px}
  .folder-outside .front .brand .sub{font-size:6.6px;letter-spacing:2.4px}
  .folder-inside{left:620px}
  .folder-inside .panel{background:linear-gradient(180deg,#f4f4f4,#e4e4e4)}
  .folder-inside .panel + .panel{border-left:1px solid #c8c8c8}
  .folder-inside .pocket{position:absolute;left:0;right:0;bottom:0;height:120px;background:linear-gradient(90deg,#0b63b3,#0a55a0)}
  .folder-inside .left .pocket{clip-path:polygon(0 8%,100% 0,100% 100%,0 100%)}
  .folder-inside .right .pocket{clip-path:polygon(0 10%,100% 0,100% 100%,0 100%)}
</style>
</head>
<body>

<!-- Business card front -->
<section class="piece card card-front">
  <svg class="art" viewBox="0 0 325 185" aria-hidden="true">
    <defs>
      <linearGradient id="cardBlue" x1="0" y1="0" x2="1" y2="0">
        <stop offset="0" stop-color="#19c0ef"/>
        <stop offset="1" stop-color="#0b6cc0"/>
      </linearGradient>
    </defs>
    <path d="M0 0 H206 Q128 92 206 185 H0 Z" fill="url(#cardBlue)"/>
    <path d="M206 0 Q128 92 206 185" fill="none" stroke="#1ebc9c" stroke-width="2.2"/>
  </svg>
  <div class="abs doctor">Gordon Patel, DDS</div>
  <div class="abs address">4817 NW Maple Crest Rd Unit B<br>Harbor Vale, ST 00000</div>
  <ul class="abs contacts">
    <li><svg viewBox="0 0 10 10"><path d="M1 3 Q5 0 9 3 L8 4.5 H6.5 L6 3.5 H4 L3.5 4.5 H2 Z M2.5 5 H7.5 L8.5 9 H1.5 Z"/></svg>555-318-2790</li>
    <li><svg viewBox="0 0 10 10"><path d="M1 3 H9 V9 H1 Z M1 3 L5 6 L9 3" stroke="currentColor" fill="none"/></svg>info@brighthavendental.example</li>
    <li><svg viewBox="0 0 10 10"><circle cx="5" cy="5" r="4.5"/></svg>www.brighthavendental.example</li>
  </ul>
  <div class="brand"><span class="name">Bright Haven</span><span class="sub">Dental Implant Center</span></div>
</section>

<!-- Appointment card -->
<section class="piece card appt">
  <div class="band"></div>
  <div class="brand white"><span class="name">Bright Haven</span><span class="sub">Dental Implant Center</span></div>
  <div class="rule"></div>
  <div class="tab">APPOINTMENT</div>
  <div class="dash"></div>
  <div class="fields">DATE :<span class="line"></span>TIME :<span class="line"></span></div>
  <p class="notice">If you are unable to keep this appointment please notify us at least<br><strong>48 hours</strong> in advance to avoid a broken appointment charge</p>
</section>

<!-- Letterhead -->
<section class="piece letter">
  <div class="brand"><span class="name">Bright Haven</span><span class="sub">Dental Implant Center</span></div>
  <div class="abs head-info">
    4817 NW Maple Crest Rd Unit B<br>Harbor Vale, ST 00000
    <ul class="contacts">
      <li><svg viewBox="0 0 10 10"><path d="M1 3 Q5 0 9 3 L8 4.5 H6.5 L6 3.5 H4 L3.5 4.5 H2 Z M2.5 5 H7.5 L8.5 9 H1.5 Z"/></svg>555-318-2790</li>
      <li><svg viewBox="0 0 10 10"><path d="M1 2 H9 V9 H1 Z"/></svg>info@brighthavendental.example</li>
      <li><svg viewBox="0 0 10 10"><circle cx="5" cy="5" r="4.5"/></svg><span class="web">www.brighthavendental.example</span></li>
    </ul>
  </div>
  <div class="abs head-rule"></div>
  <div class="ghost-circle" aria-hidden="true"></div>
  <div class="abs greet">Dear Mr. Lorne,</div>
  <div class="abs body">
    <p>Thank you for choosing our practice for your implant care. This letter confirms the details of your upcoming consultation and outlines what you can expect during your first visit with our team, from the moment you arrive at the front desk until you leave with a clear plan and a follow-up date that suits your schedule and needs.</p>
    <p>Please bring a photo ID, your insurance card and a list of current medications. Arrive fifteen minutes early so we can review your health history and answer any questions before treatment begins. Our staff will help you complete any remaining forms and make sure you feel comfortable and informed throughout.</p>
    <p>Our doctor will examine your bite, take digital scans and discuss a plan suited to your goals. We will also go over timing, costs and financing options so every step is clear to you, and we will share written notes you can take home to review with your family before deciding on next steps.</p>
    <p>If you need to change your appointment, call our office and we will gladly find a new time that works for you. We look forward to meeting you soon.</p>
  </div>
  <div class="abs close">Sincerely,</div>
  <div class="abs sign" role="img" aria-label="Handwritten signature"></div>
</section>

<!-- Envelope back -->
<section class="piece env-back">
  <div class="brand"><span class="name">Bright Haven</span><span class="sub">Dental Implant Center</span></div>
  <div class="abs address">4817 NW Maple Crest Rd Unit B<br>Harbor Vale, ST 00000</div>
  <div class="ghost-circle" aria-hidden="true"></div>
</section>

<!-- Envelope front -->
<section class="piece env-front">
  <div class="flap"></div>
  <div class="brand white"><span class="name">Bright Haven</span><span class="sub">Dental Implant Center</span></div>
</section>

<!-- Presentation folder, outside -->
<section class="folder folder-outside">
  <div class="panel back">
    <ul class="abs contacts">
      <li>4817 NW Maple Crest Rd Unit B, Harbor Vale, ST 00000</li>
      <li>555-318-2790 &nbsp;·&nbsp; info@brighthavendental.example &nbsp;·&nbsp; www.brighthavendental.example</li>
    </ul>
  </div>
  <div class="panel front">
    <div class="ghost-circle" aria-hidden="true"></div>
    <div class="brand white"><span class="name">Bright Haven</span><span class="sub">Dental Implant Center</span></div>
  </div>
</section>

<!-- Presentation folder, inside -->
<section class="folder folder-inside">
  <div class="panel left"><div class="pocket"></div></div>
  <div class="panel right"><div class="pocket"></div></div>
</section>

</body>
</html>
```